Parcelwise HQ letterhead and envelope

Design a formal (8.5x11) letterhead and envelope for sales outreach and legal matters. Using design input from https://www.parcelwisehq.example/ and the attached documents.

Industry/Entity Type

Software Service

Requirements
Must have
• These 4 hex colors are our official colors:
• #355c98 [blue]
• #1eb1a2 [teal]
• #fdba12 [gold]
• #f1653b [orange]
• So no other colors besides these should be used.

```html
<!DOCTYPE html>
<html lang="en">
<head>
<meta charset="UTF-8">
<title>Parcelwise HQ – Letterhead and Envelope</title>
<link rel="stylesheet" href="https://fonts.googleapis.com/css2?family=Open+Sans:wght@400;600&display=swap">
<style>
  :root {
    --blue: #355c98;
    --teal: #1eb1a2;
    --gold: #fdba12;
    --orange: #f1653b;
    --paper: #f0f0f0;
    --backdrop: #d4d4d4;
    --ink-dark: #3a3a3a;
    --ink-soft: #8a8a8a;
    --rule: #b8b8b8;
  }
  * { box-sizing: border-box; margin: 0; padding: 0; }
  html, body {
    width: 1200px; height: 946px; overflow: hidden;
    background: var(--backdrop);
    font-family: "Open Sans", Arial, sans-serif;
  }
  .canvas { position: relative; width: 1200px; height: 946px; }

  .sheet, .envelope {
    position: absolute;
    background: var(--paper);
    overflow: hidden;
  }

  /* brand lockup */
  .brand { position: absolute; display: flex; align-items: center; color: var(--blue); font-weight: 400; white-space: nowrap; }
  .brand-dot { border: 3px solid var(--blue); border-radius: 50%; flex: none; }
  .brand-name { letter-spacing: 0.2px; }

  /* contact blocks */
  .contact {
    position: absolute;
    font-style: normal;
    font-size: 8px;
    line-height: 11px;
    white-space: nowrap;
  }
  .contact-personal { color: var(--ink-dark); font-weight: 600; }
  .contact-office { color: var(--ink-soft); font-weight: 400; }

  /* letterhead */
  .letterhead { left: 107px; top: 148px; width: 478px; height: 672px; }
  .letterhead .brand { left: 29px; top: 46px; }
  .letterhead .brand-dot { width: 32px; height: 32px; margin-right: 9px; }
  .letterhead .brand-name { font-size: 21px; }
  .letterhead .contact-personal { left: 238px; top: 46px; }
  .letterhead .contact-divider { position: absolute; left: 364px; top: 47px; width: 1px; height: 30px; background: var(--rule); }
  .letterhead .contact-office { left: 374px; top: 46px; }

  .watermark { position: absolute; border-radius: 50%; border-style: solid; border-color: var(--blue); opacity: 0.16; }
  .letterhead .watermark { left: 147px; top: 280px; width: 184px; height: 184px; border-width: 8px; }

  /* envelope back */
  .envelope-back { left: 630px; top: 314px; width: 475px; height: 237px; }
  .flap { position: absolute; left: 0; top: 0; width: 475px; height: 72px; }
  .envelope-back .brand { left: 50%; top: 24px; transform: translateX(-50%); }
  .envelope-back .brand-dot { width: 24px; height: 24px; margin-right: 7px; }
  .envelope-back .brand-name { font-size: 15px; }

  /* envelope front */
  .envelope-front { left: 629px; top: 584px; width: 476px; height: 237px; }
  .envelope-front .brand { left: 23px; top: 30px; }
  .envelope-front .brand-dot { width: 26px; height: 26px; margin-right: 7px; }
  .envelope-front .brand-name { font-size: 18px; }
  .envelope-front .contact-personal { left: 26px; top: 81px; line-height: 10.5px; }
  .envelope-front .contact-office { left: 26px; top: 118px; line-height: 10.5px; }
  .envelope-front .watermark { left: 353px; top: 113px; width: 122px; height: 122px; border-width: 5px; }
</style>
</head>
<body>
<main class="canvas">

  <section class="sheet letterhead" aria-label="Letterhead">
    <div class="brand">
      <span class="brand-dot"></span>
      <span class="brand-name">Parcelwise HQ</span>
    </div>
    <address class="contact contact-personal">
      (555) 014-2281<br>
      jreed@parcelwisehq.example<br>
      www.parcelwisehq.example
    </address>
    <span class="contact-divider"></span>
    <address class="contact contact-office">
      Main: (555) 019-4470<br>
      88 Linden Court<br>
      Fairview, OR 97000
    </address>
    <span class="watermark"></span>
  </section>

  <section class="envelope envelope-back" aria-label="Envelope back">
    <svg class="flap" viewBox="0 0 475 72" role="img" aria-label="Envelope flap with a scattered pattern of small icons and confetti shapes">
      <defs>
        <linearGradient id="flapTone" x1="0" y1="0" x2="1" y2="0">
          <stop offset="0" stop-color="#1eb1a2" stop-opacity="0.10"/>
          <stop offset="0.35" stop-color="#f1653b" stop-opacity="0.12"/>
          <stop offset="0.65" stop-color="#fdba12" stop-opacity="0.12"/>
          <stop offset="1" stop-color="#f1653b" stop-opacity="0.10"/>
        </linearGradient>
      </defs>
      <path d="M0 0 H475 L466 60 Q464 69 454 69 H21 Q11 69 9 60 Z" fill="#f6f6f6"/>
      <path d="M0 0 H475 L466 60 Q464 69 454 69 H21 Q11 69 9 60 Z" fill="url(#flapTone)"/>
      <path d="M9 60 Q11 69 21 69 H454 Q464 69 466 60" fill="none" stroke="#c9c9c9" stroke-width="1"/>
    </svg>
    <div class="brand">
      <span class="brand-dot"></span>
      <span class="brand-name">Parcelwise HQ</span>
    </div>
  </section>

  <section class="envelope envelope-front" aria-label="Envelope front">
    <div class="brand">
      <span class="brand-dot"></span>
      <span class="brand-name">Parcelwise HQ</span>
    </div>
    <address class="contact contact-personal">
      (555) 014-2281<br>
      jreed@parcelwisehq.example<br>
      parcelwisehq.example
    </address>
    <address class="contact contact-office">
      Main: (555) 019-4470<br>
      88 Linden Court<br>
      Fairview, OR 97000
    </address>
    <span class="watermark"></span>
  </section>

</main>
</body>
</html>
```